KDWB Business Card

Looking for a business card design to incorporate our branding. We want to only use the colors listing in the Branding Package (attached).
Updates

Target Market(s)

People who need their phone or device fixed.

Industry/Entity Type

Electronics

Contact Information for Business Card

Please use:

Brightwick Gadget Clinic LLC
4810 E Harlow Ridge Rd
Suite 417
San Antonio, TX 78163

Marcus Delgrove, Store Manager

(210) 555-0147

Requirements
Must have
• Must include the colors that are contained within the Branding Package PDF file.

```html
<!DOCTYPE html>
<html lang="en">
<head>
<meta charset="utf-8">
<title>Brightwick Gadget Clinic – Business Card</title>
<link rel="stylesheet" href="https://fonts.googleapis.com/css2?family=Roboto:wght@300;400&display=swap">
<style>
  :root {
    --orange: #e8542a;
    --lime: #c7d43a;
    --ink: #0c0c0c;
    --slate: #5b5c5f;
    --paper: #ffffff;
    --mist: #eef0f2;
    --blue: #3a6cc2;
    --soft-text: #d9d9d9;
    --stage: #e7e5e1;
  }
  * { box-sizing: border-box; margin: 0; padding: 0; }
  html, body {
    width: 1200px; height: 902px; overflow: hidden;
    background: var(--stage);
    font-family: "Roboto", Arial, sans-serif;
    font-weight: 300;
  }
  .card {
    position: absolute; left: 250px; width: 700px; height: 400px;
    box-shadow: 0 6px 18px rgba(0,0,0,.18);
    overflow: hidden;
  }
  /* front face */
  .card--front { top: 40px; background: var(--paper); }
  .front-photo {
    position: absolute; inset: 0;
    background: linear-gradient(180deg, var(--mist) 0%, #dfe3e8 42%, #6d8fc9 62%, var(--blue) 100%);
  }
  .front-band {
    position: absolute; left: 0; right: 0; top: 160px; height: 110px;
    background: rgba(255,255,255,.93);
    border-top: 1px solid #d4d8de; border-bottom: 1px solid #d4d8de;
  }
  .brand {
    position: absolute; display: flex; align-items: center; gap: 16px;
  }
  .brand__mark {
    width: 62px; height: 62px; border-radius: 12px; background: var(--orange);
  }
  .brand__name {
    color: var(--orange); font-size: 30px; font-weight: 300; letter-spacing: .5px;
  }
  .card--front .brand { left: 110px; top: 184px; }

  /* back face */
  .card--back { top: 462px; background: var(--paper); padding: 8px; }
  .back-panel {
    position: relative; width: 100%; height: 100%;
    background: var(--ink);
  }
  .back-panel__edge {
    position: absolute; left: 0; right: 0; bottom: 0; height: 14px; background: var(--slate);
  }
  .back-panel__tab {
    position: absolute; left: 0; bottom: 40px; width: 8px; height: 34px; background: var(--orange);
  }
  .card--back .brand { left: 50%; top: 66px; transform: translateX(-50%); white-space: nowrap; }

  .person {
    position: absolute; right: 360px; top: 210px; text-align: right; color: var(--soft-text);
  }
  .person__name { font-size: 27px; color: #e4e4e4; }
  .person__role { font-size: 15px; color: var(--orange); margin-top: 2px; }
  .person__address { font-size: 14px; line-height: 1.45; margin-top: 18px; color: #bdbdbd; }

  .divider {
    position: absolute; left: 340px; top: 200px; width: 2px; height: 150px; background: #e0e0e0;
  }

  .contacts {
    position: absolute; left: 368px; top: 212px; list-style: none; color: var(--soft-text); font-size: 15px;
  }
  .contacts li { display: flex; align-items: center; gap: 10px; margin-bottom: 14px; }
  .contacts li.is-spaced { margin-top: 22px; }
  .contact-icon {
    width: 16px; height: 16px; background: var(--orange); border-radius: 2px;
    display: inline-flex; align-items: center; justify-content: center; flex: none;
  }
</style>
</head>
<body>

  <section class="card card--front" aria-label="Business card front">
    <div class="front-photo" role="img" aria-label="Photo of hands repairing an opened smartphone on a blue work mat"></div>
    <div class="front-band"></div>
    <div class="brand">
      <span class="brand__mark"></span>
      <span class="brand__name">Brightwick Gadget Clinic</span>
    </div>
  </section>

  <section class="card card--back" aria-label="Business card back">
    <div class="back-panel">
      <div class="brand">
        <span class="brand__mark"></span>
        <span class="brand__name">Brightwick Gadget Clinic</span>
      </div>

      <div class="person">
        <p class="person__name">Marcus Delgrove</p>
        <p class="person__role">Store Manager</p>
        <p class="person__address">4810 E Harlow Ridge Rd<br>Suite 417<br>San Antonio, TX 78163</p>
      </div>

      <div class="divider"></div>

      <ul class="contacts">
        <li>
          <span class="contact-icon">
            <svg width="10" height="10" viewBox="0 0 10 10"><path d="M2 1 L4 1 L4.5 3 L3.4 3.8 Q4.3 5.7 6.2 6.6 L7 5.5 L9 6 L9 8 Q8.6 9 7.5 9 Q1 8 1 2.5 Q1 1.4 2 1 Z" fill="#fff"/></svg>
          </span>
          (210) 555-0147
        </li>
        <li class="is-spaced">
          <span class="contact-icon">
            <svg width="10" height="8" viewBox="0 0 10 8"><rect x=".5" y=".5" width="9" height="7" fill="none" stroke="#fff"/><path d="M.5 .5 L5 4.5 L9.5 .5" fill="none" stroke="#fff"/></svg>
          </span>
          marcus@brightwickclinic.com
        </li>
        <li>
          <span class="contact-icon">
            <svg width="10" height="10" viewBox="0 0 10 10"><circle cx="5" cy="5" r="4" fill="none" stroke="#fff"/><ellipse cx="5" cy="5" rx="1.8" ry="4" fill="none" stroke="#fff"/><path d="M1 5 H9" stroke="#fff"/></svg>
          </span>
          www.brightwickclinic.com
        </li>
      </ul>

      <div class="back-panel__tab"></div>
      <div class="back-panel__edge"></div>
    </div>
  </section>

</body>
</html>
```